We need letterhead, Business Cards, and envelops designed. We have attached a design of our logo and a sample of letterhead idea that was started but never perfected, it is only an idea for the letterhead if you can design something better we may love that also we are open to change.
We want a design that looks professional in style. we are a non profit trade association in the construction industry. the green color in the attached design represent green building, and we like that. also if you just want to enhance the letterhead sample that we attached that would be fine also.
Thanks and good luck
also the name that should show on the first business cards should be Morgan Feltwick, Director are web address is www.pvtrn.org

```html
<!DOCTYPE html>
<html lang="en">
<head>
<meta charset="utf-8">
<title>PVTRN Business Card</title>
<link rel="stylesheet" href="https://fonts.googleapis.com/css2?family=Cinzel:wght@500&family=Didact+Gothic&display=swap">
<style>
  :root {
    --page-bg: #e4e4e2;
    --card-bg: #f4f4f3;
    --ink: #1c1c1c;
    --ink-soft: #3a3a3a;
    --rule: #8a8a8a;
    --brand-green: #3e7d22;
  }
  * { margin: 0; padding: 0; box-sizing: border-box; }
  html, body {
    width: 1200px;
    height: 900px;
    overflow: hidden;
    background: var(--page-bg);
  }
  .canvas {
    position: relative;
    width: 1200px;
    height: 900px;
    display: flex;
    align-items: center;
    justify-content: center;
  }
  .business-card {
    position: relative;
    width: 840px;
    height: 480px;
    background: var(--card-bg);
    box-shadow: 0 10px 30px rgba(0, 0, 0, 0.18);
    overflow: hidden;
    font-family: "Didact Gothic", "Century Gothic", sans-serif;
    color: var(--ink);
  }
  .brand {
    position: absolute;
    left: 70px;
    top: 56px;
    display: flex;
    align-items: center;
    gap: 16px;
  }
  .brand-mark {
    width: 34px;
    height: 34px;
    background: var(--brand-green);
  }
  .brand-name {
    font-size: 68px;
    line-height: 1;
    letter-spacing: 2px;
    color: var(--ink);
  }
  .holder {
    position: absolute;
    left: 70px;
    top: 168px;
  }
  .holder-name {
    font-family: "Cinzel", serif;
    font-weight: 500;
    font-size: 24px;
    letter-spacing: 3px;
    text-transform: uppercase;
    color: var(--ink);
  }
  .holder-title {
    margin-top: 4px;
    font-size: 17px;
    font-style: italic;
    letter-spacing: 1px;
    color: var(--brand-green);
  }
  .divider {
    position: absolute;
    left: 60px;
    top: 248px;
    width: 680px;
    height: 1px;
    background: var(--rule);
  }
  .address {
    position: absolute;
    left: 70px;
    top: 274px;
    font-size: 18px;
    line-height: 27px;
    letter-spacing: 1px;
    color: var(--ink-soft);
  }
  .contact-list {
    position: absolute;
    left: 360px;
    top: 274px;
    list-style: none;
    font-size: 19px;
    line-height: 29px;
    letter-spacing: 1.5px;
    color: var(--ink);
  }
  .contact-list li {
    display: flex;
    align-items: center;
    gap: 18px;
  }
  .contact-icon {
    width: 14px;
    height: 14px;
    flex: none;
  }
  .accent-band {
    position: absolute;
    right: 0;
    bottom: 0;
    width: 400px;
    height: 62px;
  }
</style>
</head>
<body>
<main class="canvas">
  <article class="business-card">
    <header class="brand">
      <span class="brand-name">PVTRN</span>
      <span class="brand-mark"></span>
    </header>

    <section class="holder">
      <h1 class="holder-name">Morgan Feltwick</h1>
      <p class="holder-title">Director</p>
    </section>

    <div class="divider"></div>

    <address class="address">
      address<br>
      4321 first street<br>
      anytown, State ZIP
    </address>

    <ul class="contact-list">
      <li>
        <svg class="contact-icon" viewBox="0 0 14 14" aria-hidden="true">
          <path d="M3 1 L5 1 L6 4 L4.5 5.2 Q5.8 8 8.8 9.5 L10 8 L13 9 L13 11 Q13 13 11 13 Q1 12 1 3 Q1 1 3 1 Z" fill="#3e7d22"/>
        </svg>
        <span>123-456-7890</span>
      </li>
      <li>
        <svg class="contact-icon" viewBox="0 0 14 14" aria-hidden="true">
          <rect x="1" y="4" width="12" height="9" rx="1" fill="#3e7d22"/>
          <rect x="3" y="1" width="8" height="4" fill="#3e7d22"/>
          <rect x="3" y="7" width="8" height="1.4" fill="#f4f4f3"/>
        </svg>
        <span>123-456-7891</span>
      </li>
      <li>
        <svg class="contact-icon" viewBox="0 0 14 14" aria-hidden="true">
          <circle cx="7" cy="7" r="6" fill="none" stroke="#3e7d22" stroke-width="1.6"/>
          <path d="M1 7 H13 M7 1 Q3 7 7 13 M7 1 Q11 7 7 13" fill="none" stroke="#3e7d22" stroke-width="1.2"/>
        </svg>
        <span>www.pvtrn.org</span>
      </li>
    </ul>

    <svg class="accent-band" viewBox="0 0 400 62" preserveAspectRatio="none" aria-hidden="true">
      <polygon points="0,0 400,0 400,62 40,62" fill="#3e7d22"/>
    </svg>
  </article>
</main>
</body>
</html>
```